Business card design and logo for hot water plumbing business

I need a logo and business card for my business which installs hot water heaters
Must have on front:
Bramblefield Hot Water Solutions
Gareth Pennick
0417382946

Either front or back:
gareth@bramblefieldhotwatersolutions.com.au
ABN 48276153094
Licence No 583214K

On the back in point form:
Supply and installation of
• electric storage
• gas storage/instantaneous
• heat pumps
• solar heaters

Iv provided 3 examples of cards I like but open to different ideas.

```html
<!DOCTYPE html>
<html lang="en">
<head>
<meta charset="utf-8">
<title>Bramblefield Hot Water Solutions – Business Card</title>
<link href="https://fonts.googleapis.com/css2?family=Exo+2:wght@400;500;600&display=swap" rel="stylesheet">
<style>
  :root {
    --bg: #e9e7e3;
    --card: #ffffff;
    --navy: #1f3545;
    --band: #e4e6e8;
    --cyan: #1ec3e0;
    --ink: #1f2a33;
    --muted: #6f7780;
    --stripe: #2b2e31;
    --logo-blue: #1a5c8a;
  }
  * { box-sizing: border-box; margin: 0; padding: 0; }
  html, body { width: 1200px; height: 675px; overflow: hidden; }
  body {
    background: var(--bg);
    font-family: "Exo 2", Arial, sans-serif;
    color: var(--ink);
    position: relative;
  }
  .card {
    position: absolute;
    width: 540px;
    height: 310px;
    background: var(--card);
    box-shadow: 0 10px 28px rgba(0,0,0,.18);
    overflow: hidden;
  }
  .card--front { left: 40px; top: 182px; }
  .card--back  { left: 620px; top: 182px; }

  .corner-stripe {
    position: absolute;
    width: 22px;
    height: 74px;
    background: var(--stripe);
  }
  .card--front .corner-stripe { left: 34px; top: 0; }
  .card--back .corner-stripe { right: 34px; bottom: 0; }

  .timeline { position: absolute; left: 0; top: 0; width: 540px; height: 310px; }

  /* front: identity block */
  .identity {
    position: absolute;
    left: 180px; top: 26px;
    width: 360px; height: 62px;
    background: var(--navy);
    color: #fff;
    padding: 10px 22px;
  }
  .identity__name { font-size: 22px; font-weight: 500; letter-spacing: 2px; text-transform: uppercase; }
  .identity__title { font-size: 12px; letter-spacing: 2px; text-transform: uppercase; opacity: .85; margin-top: 2px; }

  .contacts {
    position: absolute;
    left: 180px; top: 88px;
    width: 360px; height: 96px;
    background: var(--band);
    display: flex;
  }
  .contacts__icons {
    width: 46px;
    background: var(--cyan);
    display: flex; flex-direction: column; justify-content: space-around; align-items: center;
    padding: 6px 0;
  }
  .icon-dot {
    width: 22px; height: 22px; border-radius: 50%;
    background: var(--navy);
    display: flex; align-items: center; justify-content: center;
  }
  .contacts__list {
    list-style: none;
    display: flex; flex-direction: column; justify-content: space-around;
    padding: 6px 14px;
    font-size: 15px;
    letter-spacing: .5px;
  }
  .contacts__list .email { font-size: 11.5px; }

  .location {
    position: absolute;
    left: 300px; top: 208px;
    width: 240px; height: 70px;
    background: var(--navy);
    color: #fff;
    display: flex;
  }
  .location__icons {
    width: 40px;
    display: flex; flex-direction: column; justify-content: space-around; align-items: center;
    padding: 8px 0;
  }
  .location__icons .icon-dot { background: #c9ced3; width: 20px; height: 20px; }
  .location__text {
    display: flex; flex-direction: column; justify-content: center;
    font-size: 11px; letter-spacing: .4px; line-height: 1.6;
  }

  /* back: brand and services */
  .brand {
    position: absolute;
    left: 50px; top: 34px;
    display: flex; align-items: center; gap: 16px;
  }
  .brand__mark {
    width: 56px; height: 56px; border-radius: 50%;
    background: var(--logo-blue);
    flex: none;
  }
  .brand__name {
    font-size: 23px; font-weight: 600;
    color: var(--logo-blue);
    line-height: 1.15;
  }
  .brand__tagline {
    position: absolute;
    left: 122px; top: 98px;
    font-size: 10px; color: var(--muted); letter-spacing: .4px;
  }
  .services {
    position: absolute;
    left: 50px; top: 132px;
    width: 400px;
  }
  .services__heading {
    font-size: 14px; font-weight: 600;
    color: var(--navy);
    letter-spacing: .5px;
    padding-bottom: 6px;
    margin-bottom: 8px;
    border-bottom: 2px solid var(--cyan);
    display: inline-block;
  }
  .services__list {
    list-style: none;
    font-size: 14px;
    line-height: 1.75;
    color: var(--ink);
  }
  .services__list li { position: relative; padding-left: 18px; }
  .services__list li::before {
    content: "";
    position: absolute;
    left: 2px; top: 9px;
    width: 7px; height: 7px; border-radius: 50%;
    background: var(--cyan);
  }
</style>
</head>
<body>

  <section class="card card--front" aria-label="Card front">
    <div class="corner-stripe"></div>
    <svg class="timeline" viewBox="0 0 540 310" aria-hidden="true">
      <line x1="0" y1="196" x2="540" y2="196" stroke="#3a3f44" stroke-width="1.5"/>
      <circle cx="200" cy="196" r="7" fill="#fff" stroke="#7a8087" stroke-width="2"/>
      <circle cx="200" cy="196" r="3" fill="#7a8087"/>
      <circle cx="330" cy="196" r="7" fill="#fff" stroke="#7a8087" stroke-width="2"/>
      <circle cx="330" cy="196" r="3" fill="#7a8087"/>
    </svg>

    <header class="identity">
      <h1 class="identity__name">Gareth Pennick</h1>
      <p class="identity__title">General Manager</p>
    </header>

    <div class="contacts">
      <div class="contacts__icons">
        <span class="icon-dot"><svg width="12" height="12" viewBox="0 0 24 24"><path fill="#fff" d="M6.6 10.8a15 15 0 0 0 6.6 6.6l2.2-2.2a1 1 0 0 1 1-.25 11.4 11.4 0 0 0 3.6.57 1 1 0 0 1 1 1V20a1 1 0 0 1-1 1A17 17 0 0 1 3 4a1 1 0 0 1 1-1h3.5a1 1 0 0 1 1 1c0 1.25.2 2.45.57 3.57a1 1 0 0 1-.25 1z"/></svg></span>
        <span class="icon-dot"><svg width="11" height="11" viewBox="0 0 24 24"><rect x="3" y="5" width="18" height="14" rx="2" fill="none" stroke="#fff" stroke-width="2.5"/></svg></span>
        <span class="icon-dot"><svg width="12" height="12" viewBox="0 0 24 24"><rect x="3" y="6" width="18" height="12" rx="1" fill="none" stroke="#fff" stroke-width="2.2"/><path d="M3 7l9 6 9-6" fill="none" stroke="#fff" stroke-width="2.2"/></svg></span>
      </div>
      <ul class="contacts__list">
        <li>0417 382 946</li>
        <li>ABN 48276153094</li>
        <li class="email">gareth@bramblefieldhotwatersolutions.com.au</li>
      </ul>
    </div>

    <div class="location">
      <div class="location__icons">
        <span class="icon-dot"><svg width="11" height="11" viewBox="0 0 24 24"><circle cx="12" cy="12" r="9" fill="none" stroke="#1f3545" stroke-width="2.5"/><path d="M3 12h18M12 3c3 3 3 15 0 18M12 3c-3 3-3 15 0 18" fill="none" stroke="#1f3545" stroke-width="2"/></svg></span>
        <span class="icon-dot"><svg width="11" height="11" viewBox="0 0 24 24"><path fill="#1f3545" d="M12 2a7 7 0 0 0-7 7c0 5 7 13 7 13s7-8 7-13a7 7 0 0 0-7-7zm0 9.5A2.5 2.5 0 1 1 12 6.5a2.5 2.5 0 0 1 0 5z"/></svg></span>
      </div>
      <div class="location__text">
        <span>www.bramblefieldhotwater.com.au</span>
        <span>14 Copperleaf Lane, Tarrow VIC</span>
        <span>Licence No 583214K</span>
      </div>
    </div>
  </section>

  <section class="card card--back" aria-label="Card back">
    <div class="brand">
      <span class="brand__mark"></span>
      <p class="brand__name">Bramblefield Hot Water<br>Solutions</p>
    </div>
    <p class="brand__tagline">Reliable hot water, installed right first time</p>

    <div class="services">
      <h2 class="services__heading">Supply and installation of</h2>
      <ul class="services__list">
        <li>electric storage</li>
        <li>gas storage/instantaneous</li>
        <li>heat pumps</li>
        <li>solar heaters</li>
      </ul>
    </div>

    <div class="corner-stripe"></div>
  </section>

</body>
</html>
```